Event flyer for Sunday night Youth Group

Need a 4 x 6 or 5 x 7 flyer for a new youth group starting on April 14. The youth group is for students in middle school and high school so it needs to look fun and cool, but not childish. I prefer it not to include pictures of people unless it's so obscure you can't really see their faces. I've uploaded some pictures of flyers I like. I've also attached a couple versions of our logo to use on the flyer.
Information the flyer needs to include:
Youth Group
Sundays, 6-8pm (beginning April 14)
Location: Marlowe's - 4219 Quarry Fern Ave N, Keizer, 97318
There will be dinner, games, friends, and a message.
Target Market(s)
Youth ages 13-18
Industry/Entity Type
Church
Font styles to use
Colors
Designer to choose colors to be used in the design.
Look and feel

```html
<!DOCTYPE html>
<html lang="en">
<head>
<meta charset="utf-8">
<title>Youth Group – Sunday Nights</title>
<link rel="stylesheet" href="https://fonts.googleapis.com/css2?family=Anton&family=Montserrat:wght@500;600&family=Yellowtail&display=swap">
<style>
  :root {
    --navy: #0d2563;
    --script-blue: #1b3d9c;
    --sun: #ffd400;
    --sun-bright: #fff200;
    --ink: #1f2a30;
    --mist: #eeeeea;
    --torn-navy: #2c3d6c;
  }
  * { margin: 0; padding: 0; box-sizing: border-box; }
  html, body { width: 857px; height: 1200px; overflow: hidden; background: #fff; }
  .flyer {
    position: relative; width: 857px; height: 1200px; overflow: hidden;
    font-family: "Montserrat", sans-serif; color: var(--navy);
    background: linear-gradient(160deg, #d9d7c4 0%, var(--mist) 40%, #f5f4ea 70%, #f3eaa8 100%);
  }
  .layer { position: absolute; inset: 0; }
  .brand-banner {
    position: absolute; left: 0; top: 54px; width: 377px; height: 92px;
    background: var(--sun);
    clip-path: polygon(0 0, 100% 0, 87.5% 100%, 0 100%);
    display: flex; align-items: center; gap: 14px; padding-left: 54px;
  }
  .brand-mark { width: 34px; height: 34px; background: var(--ink); flex: none; }
  .brand-name {
    font-weight: 600; font-size: 21px; line-height: 1.05; color: var(--ink);
    text-transform: uppercase; letter-spacing: 1px;
  }
  .tag {
    position: absolute; background: var(--sun); border-radius: 8px;
    font-weight: 500; color: var(--navy); white-space: nowrap;
    display: flex; align-items: center; justify-content: center;
  }
  .tag-day { left: 119px; top: 636px; width: 192px; height: 42px; font-size: 35px; }
  .tag-start { left: 135px; top: 774px; width: 271px; height: 30px; font-size: 23px; border-radius: 4px; }
  .tag-place { left: 479px; top: 635px; width: 216px; height: 43px; font-size: 35px; gap: 6px; }
  .tag-ages { left: 276px; top: 855px; width: 304px; height: 38px; font-size: 29px; }
  .time {
    position: absolute; left: 114px; top: 672px; font-size: 98px; font-weight: 500;
    letter-spacing: -2px; line-height: 1;
  }
  .divider { position: absolute; left: 438px; top: 633px; width: 3px; height: 187px; background: #f0c000; }
  .address {
    position: absolute; left: 486px; top: 687px; font-size: 27px; font-weight: 500;
    line-height: 31px;
  }
  .details {
    position: absolute; left: 0; width: 857px; top: 900px; text-align: center;
    font-size: 30px; font-weight: 500; line-height: 38px;
  }
  .icons { position: absolute; left: 0; top: 990px; }
</style>
</head>
<body>
<div class="flyer">

  <svg class="layer" width="857" height="1200" viewBox="0 0 857 1200">
    <defs>
      <linearGradient id="panelLeft" x1="0" y1="0" x2="0" y2="1">
        <stop offset="0" stop-color="#7d7a6c"/><stop offset="0.6" stop-color="#a9a591"/><stop offset="1" stop-color="#d8d6c8" stop-opacity="0"/>
      </linearGradient>
      <linearGradient id="panelMid" x1="0" y1="0" x2="0" y2="1">
        <stop offset="0" stop-color="#e4e4e2"/><stop offset="0.5" stop-color="#cfcfcb"/><stop offset="1" stop-color="#e8e8e3" stop-opacity="0"/>
      </linearGradient>
      <linearGradient id="panelRight" x1="0" y1="0" x2="1" y2="1">
        <stop offset="0" stop-color="#8f8c72"/><stop offset="0.5" stop-color="#c7c089"/><stop offset="1" stop-color="#ece2a0" stop-opacity="0.2"/>
      </linearGradient>
      <radialGradient id="glow" cx="0.5" cy="0.5" r="0.5">
        <stop offset="0" stop-color="#ffffff" stop-opacity="0.9"/><stop offset="1" stop-color="#ffffff" stop-opacity="0"/>
      </radialGradient>
      <linearGradient id="tornNavy" x1="0" y1="0" x2="0" y2="1">
        <stop offset="0" stop-color="#8f8a5a"/><stop offset="0.35" stop-color="#3e4a66"/><stop offset="1" stop-color="var(--torn-navy)"/>
      </linearGradient>
      <linearGradient id="tornSun" x1="0" y1="0" x2="1" y2="1">
        <stop offset="0" stop-color="#ffd400"/><stop offset="1" stop-color="#fff200"/>
      </linearGradient>
    </defs>

    <rect x="0" y="0" width="286" height="460" fill="url(#panelLeft)" role="img" aria-label="Photo: hands holding an open Bible"/>
    <rect x="286" y="0" width="285" height="600" fill="url(#panelMid)" role="img" aria-label="Illustration: robed figure with open arms among bright clouds"/>
    <rect x="571" y="0" width="286" height="560" fill="url(#panelRight)" role="img" aria-label="Photo: weathered wooden cross against a cloudy sky"/>
    <ellipse cx="440" cy="850" rx="360" ry="300" fill="url(#glow)" role="img" aria-label="Soft clouds over an open Bible"/>

    <path fill="url(#tornNavy)" d="M0 505 L18 520 L30 545 L48 560 L60 590 L80 610 L88 640 L95 680 L100 720 L118 760 L132 800 L150 840 L168 880 L180 930 L205 980 L228 1030 L262 1080 L300 1120 L340 1160 L385 1200 L0 1200 Z"/>
    <path fill="url(#tornSun)" d="M857 960 L830 985 L800 995 L770 1000 L740 1003 L715 1015 L690 1040 L660 1060 L630 1075 L600 1088 L580 1110 L560 1140 L540 1170 L520 1200 L857 1200 Z"/>

    <text x="129" y="494" textLength="591" lengthAdjust="spacingAndGlyphs"
          font-family="Anton, sans-serif" font-size="258" fill="var(--sun)"
          stroke="#e6b800" stroke-width="1">YOUTH</text>
    <text x="428" y="572" textLength="352" lengthAdjust="spacingAndGlyphs"
          font-family="Yellowtail, cursive" font-size="150" fill="var(--script-blue)"
          stroke="#ffffff" stroke-width="3" paint-order="stroke">Group</text>
  </svg>

  <div class="brand-banner">
    <span class="brand-mark"></span>
    <span class="brand-name">Harborlight<br>Fellowship</span>
  </div>

  <div class="tag tag-day">Sundays</div>
  <div class="time">6-8pm</div>
  <div class="tag tag-start">(beginning April 14)</div>

  <div class="divider"></div>

  <div class="tag tag-place">Location
    <svg width="28" height="34" viewBox="0 0 28 34" fill="none" stroke="var(--navy)" stroke-width="2.4">
      <path d="M14 3 C8 3 4 7.5 4 13 C4 20 14 28 14 28 C14 28 24 20 24 13 C24 7.5 20 3 14 3 Z"/>
      <circle cx="14" cy="13" r="4"/>
      <ellipse cx="14" cy="30" rx="11" ry="2.5"/>
    </svg>
  </div>
  <div class="address">Marlowe's - 4219 Quarry<br>Fern Ave N,<br>Keizer, 97318</div>

  <div class="tag tag-ages">Youth ages 13-18</div>
  <p class="details">There will be dinner, games,<br>friends, and a message.</p>

  <svg class="icons" width="857" height="90" viewBox="0 0 857 90" fill="none" stroke="var(--navy)" stroke-width="2.6" stroke-linecap="round" stroke-linejoin="round">
    <g class="icon-dinner">
      <path d="M219 25 L219 70 M216 25 L222 25 M219 10 C216 15 219 20 219 20 C219 20 222 15 219 10"/>
      <path d="M226 38 L240 38 C240 48 236 52 233 52 C230 52 226 48 226 38 Z M233 52 L233 70 M226 70 L240 70"/>
      <path d="M236 68 C238 52 252 42 264 42 C276 42 286 52 286 68 Z M262 42 L262 37 M258 37 L266 37 M215 72 L289 72"/>
    </g>
    <line x1="310" y1="18" x2="310" y2="85" stroke="#f0c000"/>
    <g class="icon-friends">
      <circle cx="350" cy="40" r="6"/><circle cx="396" cy="40" r="6"/>
      <path d="M338 70 L338 58 C338 52 344 49 350 49 C356 49 360 52 373 38 C386 52 390 49 396 49 C402 49 408 52 408 58 L408 70"/>
      <path d="M373 14 L373 22 M360 20 L364 25 M386 20 L382 25"/>
    </g>
    <line x1="431" y1="18" x2="431" y2="85" stroke="#f0c000"/>
    <g class="icon-games">
      <path d="M472 40 C466 40 460 46 459 54 C457 64 460 72 466 72 C472 72 476 62 483 62 L505 62 C512 62 516 72 522 72 C528 72 531 64 529 54 C528 46 522 40 516 40 Z"/>
      <path d="M478 48 L478 58 M473 53 L483 53"/>
      <circle cx="510" cy="48" r="2.5"/><circle cx="510" cy="58" r="2.5"/><circle cx="505" cy="53" r="2.5"/><circle cx="515" cy="53" r="2.5"/>
    </g>
    <line x1="557" y1="18" x2="557" y2="85" stroke="#f0c000"/>
    <g class="icon-message">
      <path d="M614 14 C631 14 644 26 644 42 C644 58 631 70 614 70 C608 70 603 69 598 66 L586 70 L590 60 C586 55 584 49 584 42 C584 26 597 14 614 14 Z"/>
      <circle cx="603" cy="42" r="1.5" fill="var(--navy)"/><circle cx="614" cy="42" r="1.5" fill="var(--navy)"/><circle cx="625" cy="42" r="1.5" fill="var(--navy)"/>
    </g>
  </svg>

</div>
</body>
</html>
```